Recruitment Site Design

We need a design for the login page, about page, and inner pages of a recruitment site for an oil and gas company. Design should be modern, sleek, professional and colors can be blue, green, white, orange or any other recommended colors.

Please also take into consideration that once the users login, they will need to access a form to fill in their information.

** UPDATE: Kindly provide a design for the inner information page consistent with the outer design. Attached is a picture of the basic structure. ***
Updates

Please provide a design for inner pages as shown in the design brief consistent with the registration page provided. 

Reason: We're extending it to get more inside pages.

Target Market(s)

Professionals looking for a career in the oil and gas industry in the Middle East.

Industry/Entity Type

Oil And Gas

Requirements
Must have
• Sleek design

```html
<!DOCTYPE html>
<html lang="en">
<head>
<meta charset="utf-8">
<title>NexRig – Oil &amp; Gas Careers</title>
<link rel="stylesheet" href="https://fonts.googleapis.com/css2?family=PT+Sans:wght@400;700&family=PT+Sans+Narrow:wght@400;700&family=Didact+Gothic&display=swap">
<style>
:root{
  --black:#000;
  --ink:#222;
  --text:#333;
  --muted:#555;
  --yellow:#f6c100;
  --yellow-dark:#d9a800;
  --grey-bg:#e8e8e8;
  --footer-bg:#e6e6e6;
  --footer-bottom:#ececec;
  --white:#fff;
  --rule:#d4d4d4;
  --icon:#8a8a8a;
}
*{margin:0;padding:0;box-sizing:border-box}
html,body{width:993px;height:1200px;overflow:hidden;background:var(--white)}
body{position:relative;font-family:Arial,Helvetica,sans-serif;color:var(--text)}

/* header */
.site-header{position:absolute;left:0;top:0;width:993px;height:89px;background:var(--black)}
.brand{position:absolute;left:100px;top:22px;font-family:'PT Sans',sans-serif;font-weight:700;font-size:40px;letter-spacing:2px;color:#d8d8d8}
.main-nav{position:absolute;left:412px;top:35px;display:flex}
.main-nav a{display:block;height:24px;line-height:24px;color:var(--white);text-decoration:none;font-size:10px;letter-spacing:1.6px;font-family:Arial,sans-serif}
.main-nav .active{background:linear-gradient(#fff,#cfcfcf);color:#111;border-radius:4px;padding:0 11px;font-weight:bold}
.nav-clients{margin-left:35px}.nav-employment{margin-left:46px}.nav-services{margin-left:46px}.nav-contact{margin-left:46px}

/* hero */
.hero{position:absolute;left:0;top:89px;width:993px;height:361px;background:linear-gradient(90deg,#e8e2dc 0%,#d9c2ae 25%,#f0ece8 45%,#dfe3ea 70%,#e9e1d6 100%)}
.hero-rule{position:absolute;left:0;top:450px;width:993px;height:3px;background:var(--yellow)}
.slider-dots{position:absolute;left:465px;top:429px;display:flex;gap:7px}
.slider-dots span{width:11px;height:11px;border-radius:50%;background:#333}
.slider-dots .on{background:var(--white);border:3px solid var(--yellow)}

.search-panel{position:absolute;left:631px;top:104px;width:264px;height:313px}
.panel-tab{position:absolute;top:0;height:38px;background:var(--yellow);border-radius:6px 6px 0 0;font-family:'PT Sans Narrow',sans-serif;font-weight:700;font-size:15px;color:var(--white);text-align:center;line-height:34px;letter-spacing:.5px}
.tab-search{left:2px;width:118px;clip-path:polygon(8% 0,92% 0,100% 100%,0 100%);background:linear-gradient(#f9cd1e,var(--yellow))}
.tab-login{left:135px;width:127px;clip-path:polygon(8% 0,92% 0,100% 100%,0 100%);background:linear-gradient(#f3c418,#e6b300)}
.panel-body{position:absolute;left:0;top:35px;width:264px;height:278px;background:var(--yellow);border-radius:0 6px 8px 8px}
.field-label{position:absolute;left:37px;font-size:11.5px;color:#7a5a00}
.field-input{position:absolute;left:37px;width:183px;height:24px;background:var(--white);border:1px solid #e0b000;border-radius:3px;box-shadow:inset 0 1px 2px rgba(0,0,0,.15)}
.search-btn{position:absolute;left:90px;top:210px;width:77px;height:27px;background:linear-gradient(#eab300,#d39c00);border:1px solid #fbe27a;border-radius:3px;color:var(--white);font-family:'PT Sans Narrow',sans-serif;font-weight:700;font-size:13px;letter-spacing:1px;text-align:center;line-height:25px}

/* jobs */
.jobs-tabs{position:absolute;left:98px;top:483px;width:522px;height:31px;background:var(--black)}
.jobs-tabs span{color:var(--yellow);font-family:'PT Sans',sans-serif;font-weight:700;font-size:11px;letter-spacing:.6px;line-height:31px;position:absolute}
.tab-caret{position:absolute;left:161px;top:30px;width:0;height:0;border-left:5px solid transparent;border-right:5px solid transparent;border-top:6px solid var(--black)}
.jobs-grid{position:absolute;left:99px;top:514px;width:521px;height:229px;background:var(--grey-bg)}
.grid-v{position:absolute;left:260px;top:16px;width:1px;height:198px;background:var(--rule)}
.grid-h{position:absolute;left:8px;top:111px;width:505px;height:1px;background:var(--rule)}
.job-card{position:absolute;width:255px;height:100px}
.job-thumb{position:absolute;left:0;top:0;width:81px;height:82px;border:3px solid var(--white);box-shadow:0 0 0 1px #ccc;background:linear-gradient(160deg,#b9cde2,#7c93ae 60%,#4e5d70)}
.job-title{position:absolute;left:87px;top:4px;font-family:'PT Sans',sans-serif;font-weight:700;font-size:11.5px;color:#444}
.job-loc{position:absolute;left:87px;top:17px;font-family:'PT Sans',sans-serif;font-size:10px;color:#444;font-weight:700}
.job-desc{position:absolute;left:87px;top:30px;width:170px;font-size:9.5px;line-height:12px;color:#555}
.apply-btn{position:absolute;left:87px;top:61px;width:57px;height:18px;background:var(--black);color:var(--white);border-radius:3px;font-size:10px;font-weight:bold;letter-spacing:.5px;text-align:center;line-height:18px}
.view-link{position:absolute;left:207px;top:64px;font-size:10px;font-weight:bold;color:var(--ink)}
.view-link::after,.tm-view::after{content:"";display:inline-block;margin-left:9px;border-left:5px solid var(--yellow);border-top:3.5px solid transparent;border-bottom:3.5px solid transparent}

/* resume promo */
.resume-box{position:absolute;left:644px;top:483px;width:249px;height:260px;background:var(--black);color:var(--white)}
.resume-box h2{position:absolute;left:10px;top:18px;font-family:'Didact Gothic',sans-serif;font-weight:400;font-size:22.5px;line-height:28px;letter-spacing:.2px;white-space:nowrap}
.resume-box p{position:absolute;left:10px;top:112px;width:232px;font-size:9px;line-height:12px;color:#ddd}
.post-btn{position:absolute;left:66px;top:213px;width:108px;height:27px;background:var(--white);display:flex}
.post-btn span{flex:1;color:var(--black);font-family:'PT Sans',sans-serif;font-size:14px;line-height:27px;padding-left:6px}
.post-btn i{width:26px;background:var(--yellow);position:relative}
.post-btn i::after{content:"";position:absolute;left:9px;top:8px;border-left:9px solid var(--black);border-top:6px solid transparent;border-bottom:6px solid transparent}

/* about */
.section-title{position:absolute;font-family:'PT Sans',sans-serif;font-weight:700;font-size:19px;color:#333}
.about-rule{position:absolute;left:99px;top:795px;width:521px;height:1px;background:var(--rule)}
.about-text{position:absolute;left:100px;top:806px;width:523px;font-size:9.6px;line-height:13.3px;color:#333}
.about-text p{margin-bottom:13px}
.about-text .lead{font-weight:bold;color:#000}

/* testimonial */
.tm-rule{position:absolute;left:644px;top:796px;width:249px;height:1px;background:var(--rule)}
.tm-divider{position:absolute;left:842px;top:772px;width:1px;height:16px;background:var(--rule)}
.tm-view{position:absolute;left:852px;top:775px;font-size:10px;font-weight:bold;color:var(--ink)}
.tm-photo{position:absolute;left:712px;top:800px;width:70px;height:86px;border-radius:35px 35px 4px 4px;background:linear-gradient(#e6c07a,#c99a5e 55%,#2a2a2a)}
.tm-quote{position:absolute;left:648px;top:890px;width:248px;font-size:9.6px;line-height:12px;font-style:italic;font-weight:bold;color:#222}
.tm-name{position:absolute;left:864px;top:946px;font-size:10px;font-style:italic;font-weight:bold;color:#222}

/* footer */
.site-footer{position:absolute;left:0;top:1006px;width:993px;height:157px;background:var(--footer-bg)}
.footer-col{position:absolute;top:1011px}
.footer-col h3{font-family:'PT Sans',sans-serif;font-weight:700;font-size:11.5px;letter-spacing:.8px;color:#333}
.footer-col ul{list-style:none;margin-top:18px}
.footer-col li{font-size:9.6px;color:#444;height:20px;padding-left:2px}
.follow li{height:26.5px;display:flex;align-items:flex-start;gap:14px}
.follow li b{width:13px;height:13px;border-radius:2px;display:block;background:var(--icon)}
.partner-arrows{position:absolute;left:857px;top:1011px;display:flex;gap:2px}
.partner-arrows span{width:13px;height:12px;background:#333;position:relative}
.partner-arrows .prev::after,.partner-arrows .next::after{content:"";position:absolute;top:3px;border-top:3px solid transparent;border-bottom:3px solid transparent}
.partner-arrows .prev::after{left:4px;border-right:4px solid #fff}
.partner-arrows .next::after{left:5px;border-left:4px solid #fff}
.partner-badge{position:absolute;width:34px;height:36px;border-radius:50%}
.footer-bottom{position:absolute;left:0;top:1163px;width:993px;height:37px;background:var(--footer-bottom);border-top:1px solid #d8d8d8}
.copyright{position:absolute;left:0;top:1173px;width:993px;text-align:center;font-size:9.5px;color:#222}
</style>
</head>
<body>

<header class="site-header">
  <div class="brand">NexRig</div>
  <nav class="main-nav">
    <a class="active">HOME</a>
    <a class="nav-clients">CLIENTS</a>
    <a class="nav-employment">EMPLOYMENT</a>
    <a class="nav-services">SERVICES</a>
    <a class="nav-contact">CONTACT US</a>
  </nav>
</header>

<section class="hero" role="img" aria-label="Smiling young professional in an office with blurred colleagues behind"></section>
<div class="hero-rule"></div>
<div class="slider-dots"><span class="on"></span><span></span><span></span><span></span></div>

<div class="search-panel">
  <div class="panel-tab tab-login">LOGIN</div>
  <div class="panel-body">
    <div class="field-label" style="top:37px">Enter Keyword:</div>
    <div class="field-input" style="top:56px"></div>
    <div class="field-label" style="top:93px">Industry :</div>
    <div class="field-input" style="top:112px"></div>
    <div class="field-label" style="top:149px;left:35px">Location:</div>
    <div class="field-input" style="top:170px"></div>
    <div class="search-btn">SEARCH</div>
  </div>
  <div class="panel-tab tab-search">JOB SEARCH</div>
</div>

<div class="jobs-tabs">
  <span style="left:43px">NEW JOBS</span>
  <span style="left:184px">JOBS BY INDUSTRY</span>
  <span style="left:371px">JOBS BY LOCATION</span>
  <div class="tab-caret"></div>
</div>
<div class="jobs-grid">
  <div class="grid-v"></div>
  <div class="grid-h"></div>

  <div class="job-card" style="left:6px;top:18px">
    <div class="job-thumb" role="img" aria-label="Engineers on an offshore platform deck"></div>
    <div class="job-title">NEW JOB TITLE</div>
    <div class="job-loc">Location: Middle East</div>
    <div class="job-desc">veritatis et quasi architecto bea vitae dicta sunt explicit aspernatur aut odit</div>
    <div class="apply-btn">APPLY</div>
    <div class="view-link">VIEW</div>
  </div>
  <div class="job-card" style="left:268px;top:18px">
    <div class="job-thumb" role="img" aria-label="Engineers on an offshore platform deck"></div>
    <div class="job-title">NEW JOB TITLE</div>
    <div class="job-loc">Location: Middle East</div>
    <div class="job-desc">veritatis et quasi architecto bea vitae dicta sunt explicit aspernatur aut odit</div>
    <div class="apply-btn">APPLY</div>
    <div class="view-link">VIEW</div>
  </div>
  <div class="job-card" style="left:6px;top:128px">
    <div class="job-thumb" role="img" aria-label="Engineers on an offshore platform deck"></div>
    <div class="job-title">NEW JOB TITLE</div>
    <div class="job-loc">Location: Middle East</div>
    <div class="job-desc">veritatis et quasi architecto bea vitae dicta sunt explicit aspernatur aut odit</div>
    <div class="apply-btn">APPLY</div>
    <div class="view-link">VIEW</div>
  </div>
  <div class="job-card" style="left:268px;top:128px">
    <div class="job-thumb" role="img" aria-label="Engineers on an offshore platform deck"></div>
    <div class="job-title">NEW JOB TITLE</div>
    <div class="job-loc">Location: Middle East</div>
    <div class="job-desc">veritatis et quasi architecto bea vitae dicta sunt explicit aspernatur aut odit</div>
    <div class="apply-btn">APPLY</div>
    <div class="view-link">VIEW</div>
  </div>
</div>

<aside class="resume-box">
  <h2>LOOKING FOR A JOB<br>POST YOUR RESUME<br>HERE</h2>
  <p>veritatis et quasi architect beatae vitae dictnt expli-cabo. Nemo enim ipsam voluptatem quia voluptas sit aspernatur aut odit aut fugit, sed quia cnsequun-tur magni dolores eo veritatis et quasi itecto beatae vitae dicta sunt explicabo. Nemo enim ipsam volup-tatem quia voluptas sit aspernatur aut odit aut fugit, sed quia consequuntur magni dolores eo</p>
  <div class="post-btn"><span>POST NOW</span><i></i></div>
</aside>

<h2 class="section-title" style="left:100px;top:766px">What We Do ?</h2>
<div class="about-rule"></div>
<div class="about-text">
  <p class="lead">mpora incidunt ut labore et dolore magnam aliquam quaerat voluptatem. Ut enim ad minima ven quis nostrum exercitationem ullam corporis suscipit laboriosam,</p>
  <p>Sed ut perspiciatis unde omnis iste natus error sit voluptatem accusantium doloremque laudantium, torm rem aperiam, eaque ipsa quae ab illo inventore veritatis et quasi architecto beatae vitae dicta sunt explicabo. Nemo sam voluptatem quia voluptas sit aspernatur aut odit aut fugit, sed quia consequuntur magni dolores eos qui ratione voil sequi nesciunt. Neque porro quisquam est, qui dolorem ipsum quia dolor sit amet, consectetur,</p>
  <p>adipisci velit, sed quia nnumquam eius modi tempora incidunt ut labore et dolore magnam aliquam quaerat volupttem. Ut enim ad minima ven quis nostrum exercitationem ullam corporis suscipit laboriosam, nisi ut aliquid ex ea commodi consequatur? Quis aute vel eum iure reprehenderit qui in ea voluptate velit esse quam nihil molestiae consequatur, vel illum qui dolorem um exercitationem ullam corporis suscipit laboriosam, nisi ut aliquid ex ea commodi consequatu Quis aute vel eum iure reprehenderit qui in ea voluptate velit esse quam nihil molestiae consequatur, vel illum quidoloriliuem eum</p>
</div>

<h2 class="section-title" style="left:644px;top:766px">Testimonials</h2>
<div class="tm-divider"></div>
<div class="tm-view">VIEW</div>
<div class="tm-rule"></div>
<div class="tm-photo" role="img" aria-label="Portrait of a smiling businesswoman"></div>
<p class="tm-quote">"Lorem ipsum dolor sit amet, consectetur adipisic-ing elit, sed do eiusmod tempor incididunt ut labore et dolore magna aliqua. Ut enim ad minim veniam, quis nostrud exercitation ullamco laboris nisi ut"</p>
<div class="tm-name">-KARIM</div>

<footer>
  <div class="site-footer"></div>
  <div class="footer-col" style="left:99px">
    <h3>INFORMATION</h3>
    <ul><li>Home</li><li>Sitemap</li><li>Search Jobs</li><li>View Jobs</li><li>Contact</li></ul>
  </div>
  <div class="footer-col" style="left:297px">
    <h3>SUPPORT</h3>
    <ul><li>Report aProblem</li><li>About NexRig</li><li>Privacy Policy</li><li>Get Jobs On Mobile</li><li>Post A Resume</li></ul>
  </div>
  <div class="footer-col follow" style="left:496px">
    <h3>FOLLOW US</h3>
    <ul style="margin-top:20px">
      <li><b></b>Circlely</li>
      <li><b></b>Chirper</li>
      <li><b></b>ProLink</li>
      <li><b></b>Rss Feed</li>
    </ul>
  </div>
  <div class="footer-col" style="left:695px"><h3>OUR PARTNERS</h3></div>
  <div class="partner-arrows"><span class="prev"></span><span class="next"></span></div>
  <div class="partner-badge" style="left:719px;top:1040px;background:#2b4a8c"></div>
  <div class="partner-badge" style="left:799px;top:1040px;background:#c9372c"></div>
  <div class="partner-badge" style="left:720px;top:1101px;background:#6a7fa6"></div>
  <div class="partner-badge" style="left:799px;top:1101px;background:#3b9ac4"></div>
  <div class="footer-bottom"></div>
  <div class="copyright">© 2012 NexRig.All rights reserved.</div>
</footer>

</body>
</html>
```